Detail Shop Business card design

i need a business card design for my new detailing company called 'Brisk's Polish Works'. i want an all black and white design . simple, direct and to the point. i want the designer to choose a fitting font to match the logothe front should have logo, address, phone and email and the back side should have a slogan and text indicating that we offer services on anything including cars, trucks, motorcycles and RVs. slogan will read "we take pride in your ride"
maybe also very small on the back side the IG icon with Brisks_Polish_Works

phone 208.417.6352
address 3847 E Larkin Ave
Spokane WA 99214
email: BrisksPolish@mailvexo.com

Target Market(s)

all ages , auto enthusiasts

Industry/Entity Type

Automotive

Contact Information for Business Card

the front should have logo, address, phone and email and the back side should have a slogan and text indicating that we offer services on anything including cars, trucks, motorcycles and RVs. slogan will read "we take pride in your ride"

phone 208.417.6352
address 3847 E Larkin Ave
Spokane WA 99214

Colors
000000
ffffff

Requirements
Must have
• bold font and very simple design with good spacing
Nice to have
• anything creative from the designer indicating we service any types of vehicles
Should not have
• any colors ,

```html
<!DOCTYPE html>
<html lang="en">
<head>
<meta charset="utf-8">
<title>Brisk's Polish Works — Business Card</title>
<link rel="stylesheet" href="https://fonts.googleapis.com/css2?family=Roboto:wght@400;500;700&family=Oswald:wght@400;500&display=swap">
<style>
  :root {
    --ink: #000000;
    --paper: #ffffff;
    --card-stock: #f4f4f4;
    --backdrop: #e6e6e6;
    --art-dark: #1a1a1a;
    --art-mid: #4a4a4a;
  }
  * { box-sizing: border-box; margin: 0; padding: 0; }
  html, body {
    width: 1200px; height: 960px; overflow: hidden;
    background: var(--backdrop);
  }
  .stage { position: relative; width: 1200px; height: 960px; }

  .card {
    position: absolute;
    width: 600px; height: 343px;
    background: var(--card-stock);
    box-shadow: 0 2px 6px rgba(0,0,0,0.25);
    overflow: hidden;
  }
  .card--front { left: 314px; top: 113px; }
  .card--back  { left: 311px; top: 472px; }

  /* Front */
  .brand {
    position: absolute; left: 58px; top: 128px; width: 210px;
    display: flex; flex-direction: column; align-items: center; gap: 14px;
  }
  .brand__dot {
    width: 26px; height: 26px; border-radius: 50%;
    background: var(--ink);
  }
  .brand__name {
    font-family: 'Roboto', sans-serif; font-weight: 700;
    font-size: 22px; line-height: 1.15; color: var(--ink);
    text-align: center; text-transform: uppercase;
  }

  .contact-panel {
    position: absolute; left: 322px; top: 66px;
    width: 278px; height: 215px;
    background: var(--ink); color: var(--paper);
    font-family: 'Roboto', sans-serif;
    padding: 19px 0 0 39px;
  }
  .contact-panel__name { font-size: 20px; font-weight: 500; line-height: 22px; }
  .contact-panel__title { font-size: 14px; line-height: 18px; letter-spacing: 0.2px; }
  .contact-panel__address { margin-top: 12px; font-size: 14px; line-height: 18px; }
  .contact-list { list-style: none; margin-top: 12px; }
  .contact-list li {
    display: flex; align-items: center; gap: 9px;
    font-size: 14px; line-height: 19.5px;
  }
  .contact-list svg { width: 13px; height: 13px; fill: var(--paper); flex: none; }

  /* Back */
  .services {
    position: absolute; top: 48px; left: 0; width: 100%;
    text-align: center;
    font-family: 'Oswald', sans-serif; font-weight: 500;
    font-size: 19px; color: var(--ink); letter-spacing: -0.2px;
  }
  .vehicle-art {
    position: absolute; left: 20px; top: 106px; width: 550px; height: 182px;
    border-radius: 70px 90px 60px 60px;
    background: linear-gradient(180deg, var(--art-mid), var(--art-dark));
  }
  .ground { position: absolute; left: 0; bottom: 0; width: 600px; height: 60px; }
  .ground path { fill: var(--ink); }
  .slogan {
    position: absolute; bottom: 17px; left: 0; width: 100%;
    text-align: center;
    font-family: 'Roboto', sans-serif; font-weight: 700;
    font-size: 16px; color: var(--paper); letter-spacing: 0.3px;
  }
</style>
</head>
<body>
<main class="stage">

  <section class="card card--front" aria-label="Card front">
    <div class="brand">
      <span class="brand__dot"></span>
      <span class="brand__name">Brisk's Polish Works</span>
    </div>

    <div class="contact-panel">
      <p class="contact-panel__name">MARA QUILL</p>
      <p class="contact-panel__title">CEO/FOUNDER</p>
      <p class="contact-panel__address">3847 E Larkin Ave<br>Spokane WA 99214</p>
      <ul class="contact-list">
        <li>
          <svg viewBox="0 0 16 16" aria-hidden="true"><path d="M3.6 1l2.6 3-1.5 1.8c.9 2 2.5 3.6 4.5 4.5L11 8.8l3 2.6-1.4 2.9C7 14 2 9 1.7 3.4z"/></svg>
          208.417.6352
        </li>
        <li>
          <svg viewBox="0 0 16 16" aria-hidden="true"><path d="M4 0h8a1 1 0 0 1 1 1v14a1 1 0 0 1-1 1H4a1 1 0 0 1-1-1V1a1 1 0 0 1 1-1zm1 2v10h6V2zm3 11a1 1 0 1 0 0 2 1 1 0 0 0 0-2z"/></svg>
          208 552 7183
        </li>
        <li>
          <svg viewBox="0 0 16 16" aria-hidden="true"><path d="M1 3h14v1.2L8 8.6 1 4.2zm0 2.6l7 4.4 7-4.4V13H1z"/></svg>
          BrisksPolish@mailvexo.com
        </li>
        <li>
          <svg viewBox="0 0 16 16" aria-hidden="true"><path d="M8 1a7 7 0 1 0 0 14A7 7 0 0 0 8 1zm-1 2.2c-.6 1-1.8 1.3-2 2.6.8.4 1.6.2 2 1 .4 1 1.6 1 1.6 2.2 0 1-1 1.6-.8 2.8C5.2 11.6 3 9.6 3 8c0-2.3 1.7-4.3 4-4.8zm3 .4c1.8.8 3 2.5 3 4.4-1-.2-1.6-1-2.6-.6-.8-.6-.2-1.8-1-2.6.4-.4.6-.8.6-1.2z"/></svg>
          www.briskspolish.com
        </li>
      </ul>
    </div>
  </section>

  <section class="card card--back" aria-label="Card back">
    <p class="services">we offer services on anything including cars, trucks, motorcycles &amp; RVs</p>
    <div class="vehicle-art" role="img" aria-label="Black and white illustration of a classic hot rod car in side view"></div>
    <svg class="ground" viewBox="0 0 600 60" preserveAspectRatio="none" aria-hidden="true">
      <path d="M0 38 C120 8 480 8 600 38 L600 60 L0 60 Z"/>
    </svg>
    <p class="slogan">WE TAKE PRIDE IN YOUR RIDE</p>
  </section>

</main>
</body>
</html>
```